Business Card Design - Service Company

Use of the card mainly in living rooms and relations b2b We wish a card with a modern design, blue tones in the background would be a plus The card must be front / back (one side with the logo / the other with the information of contact )

Font styles to use
Serif

Requirements
Must have
• Using the map on the back of the business card Editable format! Photoshop CS2 / Illustrator CS2
Nice to have
• Mivrel Data IT Plein Ouest Commercial Center, 20417 Valmorra 0491847352 Siret 41873306200018 APE 9511Z https://www.fb.com/boutiquetech.mivreldata www.mivrel-data.com

```html
<!DOCTYPE html>
<html lang="en">
<head>
<meta charset="utf-8">
<title>Mivrel Data IT – Business Card</title>
<link href="https://fonts.googleapis.com/css2?family=Lora:wght@400;600;700&display=swap" rel="stylesheet">
<style>
  :root {
    --page-bg: #e6eaef;
    --panel-black: #030303;
    --brand-blue: #1f6fc0;
    --text-light: #d9d9d9;
    --logo-grey: #3b3f46;
    --frost-top: #f4f5f7;
    --frost-bottom: #ccd3db;
  }
  html, body {
    margin: 0;
    padding: 0;
    width: 1200px;
    height: 970px;
    overflow: hidden;
    background: var(--page-bg);
    font-family: "Lora", Georgia, serif;
  }
  .business-card {
    position: absolute;
    left: 80px;
    top: 187px;
    width: 1040px;
    height: 595px;
    border-radius: 44px;
    overflow: hidden;
    background: linear-gradient(170deg, var(--frost-top) 0%, #e6e9ed 45%, var(--frost-bottom) 100%);
    box-shadow: 0 10px 30px rgba(0,0,0,.18);
  }
  .card-shapes {
    position: absolute;
    inset: 0;
  }
  .contact-side {
    position: absolute;
    left: 68px;
    top: 0;
    color: var(--text-light);
  }
  .person-name {
    position: absolute;
    top: 104px;
    margin: 0;
    font-size: 31px;
    font-weight: 600;
    color: var(--brand-blue);
    white-space: nowrap;
    letter-spacing: .3px;
  }
  .person-role {
    position: absolute;
    top: 137px;
    font-size: 24px;
    white-space: nowrap;
  }
  .company-name {
    position: absolute;
    top: 214px;
    font-size: 26px;
    font-weight: 600;
    color: var(--brand-blue);
    white-space: nowrap;
  }
  .address-line {
    position: absolute;
    font-size: 24px;
    white-space: nowrap;
  }
  .contact-list {
    position: absolute;
    top: 350px;
    margin: 0;
    padding: 0;
    list-style: none;
  }
  .contact-item {
    display: flex;
    align-items: center;
    height: 34px;
    font-size: 24px;
    white-space: nowrap;
  }
  .contact-icon {
    width: 30px;
    height: 30px;
    margin-right: 12px;
  }
  .registry-line {
    position: absolute;
    top: 480px;
    font-size: 24px;
    white-space: nowrap;
    color: #c9c9c9;
  }
  .brand-mark {
    position: absolute;
    left: 575px;
    top: 268px;
    display: flex;
    align-items: center;
    gap: 16px;
  }
  .brand-square {
    width: 26px;
    height: 26px;
    background: var(--brand-blue);
  }
  .brand-name {
    font-size: 46px;
    font-weight: 700;
    color: var(--logo-grey);
    white-space: nowrap;
  }
</style>
</head>
<body>
  <div class="business-card">
    <svg class="card-shapes" width="1040" height="595" viewBox="0 0 1040 595" aria-hidden="true">
      <path d="M0,0 H538 Q466,297 542,595 H0 Z" fill="var(--panel-black)"/>
      <path d="M544,0 Q462,297 548,595" fill="none" stroke="var(--brand-blue)" stroke-width="4"/>
      <circle cx="0" cy="135" r="32" fill="var(--brand-blue)"/>
    </svg>

    <div class="contact-side">
      <h1 class="person-name">ADRIEN MORETTI</h1>
      <div class="person-role">Director</div>
      <div class="company-name">MIVREL DATA IT</div>
      <div class="address-line" style="top:249px">Plein Ouest Commercial Center</div>
      <div class="address-line" style="top:283px">20417 Valmorra</div>

      <ul class="contact-list">
        <li class="contact-item">
          <svg class="contact-icon" viewBox="0 0 30 30" aria-hidden="true">
            <circle cx="15" cy="15" r="13" fill="none" stroke="var(--brand-blue)" stroke-width="2.5"/>
            <path d="M10.5,8.5 l3,0 l1,4 l-2,1.5 q1.5,3 4,4.5 l1.5,-2 l4,1 l0,3 q-1,1.5 -3,1.5 q-6,-1 -9.5,-8.5 q-0.5,-3 1,-5z" fill="var(--brand-blue)"/>
          </svg>
          0491847352
        </li>
        <li class="contact-item">
          <svg class="contact-icon" viewBox="0 0 30 30" aria-hidden="true">
            <circle cx="15" cy="15" r="13" fill="none" stroke="var(--brand-blue)" stroke-width="2.5"/>
            <circle cx="15" cy="15" r="7" fill="var(--brand-blue)"/>
          </svg>
          boutiquetech.mivreldata
        </li>
        <li class="contact-item">
          <svg class="contact-icon" viewBox="0 0 30 30" aria-hidden="true">
            <circle cx="15" cy="15" r="13" fill="none" stroke="var(--brand-blue)" stroke-width="2.5"/>
            <circle cx="15" cy="15" r="7.5" fill="none" stroke="var(--brand-blue)" stroke-width="1.5"/>
            <ellipse cx="15" cy="15" rx="3.2" ry="7.5" fill="none" stroke="var(--brand-blue)" stroke-width="1.3"/>
            <line x1="7.5" y1="15" x2="22.5" y2="15" stroke="var(--brand-blue)" stroke-width="1.3"/>
          </svg>
          www.mivrel-data.com
        </li>
      </ul>

      <div class="registry-line">Siret 41873306200018 APE 9511Z</div>
    </div>

    <div class="brand-mark">
      <span class="brand-name">MIVREL DATA IT</span>
      <span class="brand-square"></span>
    </div>
  </div>
</body>
</html>
```